Electrician Business Card/ company logo/small business

New Business Cards and logo needed that will catch peoples eye and say we went that extra step. Attached is a design possibly to be incorporated, if u have your own great, lets see it!... This will be a small local business. thank you for all you do!
Halvern Electric
Ned Fosky Owner
Journeyman Electrician
phone 1.555.208.3471
email: KQLHalvernElectric@quellmail.net
call for free estimate!
Updates

Accepted and approved for cards

Target Market(s)

support small local business

Industry/Entity Type

Electrical,

Contact Information for Business Card

name, title,company/ logo, phone, email, free estimate

Other font styles liked:
• easy to read

Colors

Designer to choose colors to be used in the design.

Requirements
Must have
• eye catching everything! logo and halvern electric listed on business card/logo, incorp logo in the background of card
Nice to have
• lightening bolts in eyes or around the triangle? vertical, modern, any design that would be unique and stand out
Should not have
• pinks, reds, yellows,brown

```html
<!DOCTYPE html>
<html lang="en">
<head>
<meta charset="utf-8">
<title>Halvern Electric – Business Card</title>
<link href="https://fonts.googleapis.com/css2?family=Open+Sans:wght@400;600;700&family=Open+Sans+Condensed:wght@700&display=swap" rel="stylesheet">
<style>
  :root {
    --backdrop: #6b6b6b;
    --lime: #8dc21f;
    --ice: #d6e9f1;
    --ink: #121212;
    --muted-ink: #2a2a2a;
    --white: #ffffff;
    --night: #050505;
    --storm: #3a3d40;
  }
  * { margin: 0; padding: 0; box-sizing: border-box; }
  html, body {
    width: 935px;
    height: 1200px;
    overflow: hidden;
    background: var(--backdrop);
    font-family: "Open Sans", Arial, sans-serif;
  }
  .card {
    position: absolute;
    left: 97px;
    width: 741px;
    height: 481px;
    border-radius: 34px;
    overflow: hidden;
  }

  /* Front */
  .card--front { top: 83px; background: var(--ice); }
  .brand-panel {
    position: absolute;
    left: 0; top: 0;
    width: 243px; height: 100%;
    background: var(--lime);
  }
  .brand-panel__name {
    position: absolute;
    top: 297px; left: 0; width: 100%;
    text-align: center;
    color: var(--white);
    font-family: "Open Sans Condensed", "Arial Narrow", sans-serif;
    font-weight: 700;
    font-size: 16px;
    line-height: 22px;
    letter-spacing: 0.2px;
  }
  .brand-panel__dot {
    position: absolute;
    top: 356px; left: 100px;
    width: 42px; height: 42px;
    border-radius: 50%;
    border: 4px solid var(--white);
  }
  .edge-accent {
    position: absolute;
    right: -120px; top: 50px;
    width: 230px; height: 330px;
    border-radius: 50%;
    background: var(--lime);
    box-shadow: 0 0 14px 4px rgba(140, 210, 240, 0.9);
  }
  .holder__name {
    position: absolute;
    left: 266px; top: 80px;
    font-family: "Open Sans", Arial, sans-serif;
    font-weight: 700;
    font-size: 33px;
    line-height: 46px;
    letter-spacing: -0.8px;
    transform: scaleX(0.9);
    transform-origin: left;
    color: var(--ink);
  }
  .holder__role {
    position: absolute;
    left: 270px; top: 124px;
    font-size: 20px;
    line-height: 28px;
    color: var(--lime);
  }
  .contact {
    position: absolute;
    left: 272px; top: 340px;
    list-style: none;
    font-size: 21px;
    color: var(--muted-ink);
    line-height: 36px;
  }
  .contact__label {
    display: inline-block;
    width: 31px;
    font-weight: 700;
    color: var(--lime);
  }

  /* Back */
  .card--back { top: 626px; background: var(--night); }
  .storm-backdrop {
    position: absolute;
    inset: 0;
    background:
      radial-gradient(ellipse 55% 30% at 62% 28%, rgba(120,125,130,0.55), transparent 70%),
      radial-gradient(ellipse 40% 35% at 30% 78%, rgba(90,95,100,0.45), transparent 70%),
      radial-gradient(ellipse 70% 60% at 50% 50%, var(--storm), var(--night) 75%);
  }
  .back-mark {
    position: absolute;
    left: 0; right: 0; top: 218px;
    display: flex;
    align-items: center;
    justify-content: center;
    gap: 18px;
    color: var(--white);
    font-family: "Open Sans Condensed", "Arial Narrow", sans-serif;
    font-weight: 700;
    font-size: 40px;
  }
  .back-mark__dot {
    width: 38px; height: 38px;
    border-radius: 50%;
    background: var(--white);
  }
</style>
</head>
<body>
  <section class="card card--front">
    <div class="brand-panel">
      <p class="brand-panel__name">HALVERN ELECTRIC</p>
      <span class="brand-panel__dot"></span>
    </div>
    <div class="edge-accent"></div>
    <h1 class="holder__name">Ned Fosky Journeyman</h1>
    <p class="holder__role">electrician</p>
    <ul class="contact">
      <li><span class="contact__label">P</span>1.555.208.3471</li>
      <li><span class="contact__label">E</span>KQLHalvernElectric@quellmail.net</li>
    </ul>
  </section>

  <section class="card card--back">
    <div class="storm-backdrop" role="img" aria-label="Lightning bolts across a dark night sky"></div>
    <div class="back-mark">
      <span class="back-mark__dot"></span>
      <span class="back-mark__name">HALVERN ELECTRIC</span>
    </div>
  </section>
</body>
</html>
```